****Business Card Design for Quarrystone Development. Design based around attached logo/company name

I’m looking for business card design for my company Quarrystone Development Group,LLC. Design should be professional, sharp and minimal. Outside of the attached logos, greyscale colors for remainder of cards. My thoughts are two-sided card with attached logo on one side and my info on the other but open to one-sided as well with right design.
Target Market(s)
Real estate professionals including banks, private investors, property owners, developers, commercial tenants like Brewlantern, Grovika or Tanquist’s.
Industry/Entity Type
Commercial real estate development and investments.
Contact Information for Business Card
Name, title, email, phone #’s, web address and physical address
Font styles to use
Other font styles liked:
- Helvetica, Garamond, etc
Colors
Designer to choose only greyscale colors for use in the design.
Requirements
Must have
- Attached logo first or second options.
Nice to have
- Two sided card with logo on one side. Attached Logo/company name can be laid out any way that flows as long as it’s legible.name
Should not have
- No loud colors. ***Please do not include logo, I have removed the company design with a logo image.

```html
<!DOCTYPE html>
<html lang="en">
<head>
<meta charset="UTF-8">
<title>Quarrystone Development Group, LLC — Business Card</title>
<link href="https://fonts.googleapis.com/css2?family=Cormorant+Garamond:wght@500&family=Oswald:wght@600&family=Inter:wght@400&display=swap" rel="stylesheet">
<style>
  :root {
    --stage: #161616;
    --card-light: #2c2c2d;
    --card-dark: #1c1c1d;
    --ink-white: #f2f2f2;
    --ink-silver: #c9ccd1;
    --ink-steel: #8d929b;
    --rule: #9a9a9a;
  }
  * { margin: 0; padding: 0; box-sizing: border-box; }
  html, body {
    width: 1200px; height: 900px; overflow: hidden;
    background: var(--stage);
  }
  .stage {
    width: 1200px; height: 900px;
    display: flex; flex-direction: column;
    align-items: center; justify-content: center; gap: 40px;
  }
  .card {
    position: relative;
    width: 620px; height: 354px;
    background: linear-gradient(125deg, var(--card-dark) 0%, var(--card-light) 60%, var(--card-dark) 100%);
    box-shadow: 0 18px 40px rgba(0,0,0,0.6);
  }

  /* Front */
  .card--front { display: flex; align-items: center; justify-content: center; }
  .wordmark {
    font-family: "Cormorant Garamond", Georgia, serif;
    font-weight: 500;
    color: var(--ink-silver);
    text-align: center;
    line-height: 1;
  }
  .wordmark__name {
    display: block;
    font-size: 58px; letter-spacing: 3px; text-transform: uppercase;
  }
  .wordmark__sub {
    display: block;
    margin-top: 8px;
    font-size: 20px; letter-spacing: 4px; text-transform: uppercase;
  }

  /* Back */
  .card--back .wordmark { position: absolute; top: 40px; left: 0; right: 0; }
  .card--back .wordmark__name { font-size: 40px; letter-spacing: 2px; }
  .card--back .wordmark__sub { font-size: 14px; letter-spacing: 3px; margin-top: 6px; }

  .holder {
    position: absolute; top: 160px; left: 70px; width: 200px;
    text-align: right;
  }
  .holder__name {
    font-family: "Oswald", "Arial Narrow", sans-serif;
    font-weight: 600; font-size: 30px; letter-spacing: 1.5px;
    color: var(--ink-steel); text-transform: uppercase;
  }
  .holder__title {
    margin-top: 4px;
    font-family: "Inter", Helvetica, Arial, sans-serif;
    font-size: 17px; color: var(--ink-white);
  }
  .divider {
    position: absolute; top: 162px; left: 296px;
    width: 1px; height: 80px; background: var(--rule);
  }
  .contacts {
    position: absolute; top: 166px; left: 320px;
    list-style: none;
    font-family: "Inter", Helvetica, Arial, sans-serif;
    font-size: 17px; color: var(--ink-white);
  }
  .contacts li { display: flex; align-items: center; gap: 10px; height: 25px; }
  .contacts svg { width: 14px; height: 14px; flex: none; }
  .address {
    position: absolute; bottom: 40px; left: 0; right: 0;
    text-align: center;
    font-family: "Inter", Helvetica, Arial, sans-serif;
    font-size: 17px; letter-spacing: 0.5px; color: var(--ink-white);
  }
</style>
</head>
<body>
<main class="stage">
  <section class="card card--front" aria-label="Card front">
    <h1 class="wordmark">
      <span class="wordmark__name">Quarrystone</span>
      <span class="wordmark__sub">Development Group, LLC</span>
    </h1>
  </section>

  <section class="card card--back" aria-label="Card back">
    <div class="wordmark">
      <span class="wordmark__name">Quarrystone</span>
      <span class="wordmark__sub">Development Group, LLC</span>
    </div>

    <div class="holder">
      <p class="holder__name">Daniel Hargrove</p>
      <p class="holder__title">Director</p>
    </div>

    <div class="divider"></div>

    <ul class="contacts">
      <li>
        <svg viewBox="0 0 16 16" fill="none" stroke="#8d929b" stroke-width="1.4"><path d="M4 1.5 6 5 4.6 6.4a8 8 0 0 0 5 5L11 10l3.5 2-1 2.5C7 14.5 1.5 9 1.5 2.5z"/></svg>
        (555) 014-2286
      </li>
      <li>
        <svg viewBox="0 0 16 16" fill="none" stroke="#8d929b" stroke-width="1.4"><rect x="1.5" y="3.5" width="13" height="9"/><path d="m1.5 3.5 6.5 5 6.5-5"/></svg>
        info@quarrystonegroup.com
      </li>
      <li>
        <svg viewBox="0 0 16 16" fill="none" stroke="#8d929b" stroke-width="1.2"><circle cx="8" cy="8" r="6.5"/><ellipse cx="8" cy="8" rx="3" ry="6.5"/><path d="M1.5 8h13M2.5 4.8h11M2.5 11.2h11"/></svg>
        www.quarrystonegroup.com
      </li>
    </ul>

    <p class="address">1187 Cedar Mill Lane Salem, OR 97301</p>
  </section>
</main>
</body>
</html>
```